Musical download and streaming website

hello designers, I want to start up a musical website where users can download and rate music of different genres such as RnB, Hip hop, rock, afro-pop. This website should be attractive and contemporary. There will be a search column for different songs. Music files will be mp3, mwa, and others. I like blue, gold, pink and indigo colors. My website should resemble http://tunovalt.com. There should be good imaginary of music stars on my website.

```html
<!DOCTYPE html>
<html lang="en">
<head>
<meta charset="utf-8">
<title>Honey Tunes</title>
<link href="https://fonts.googleapis.com/css2?family=Roboto:wght@300;400;500;700&display=swap" rel="stylesheet">
<style>
:root{
  --blue:#1b7fc1;
  --blue-dark:#0f5f9e;
  --gold-top:#f4e2a4;
  --gold-bot:#d8a84e;
  --ink:#333;
  --muted:#999;
  --line:#e6e6e6;
  --star:#e9c31a;
  --icon:#8a8a8a;
  --footer:#1d1d1d;
}
*{box-sizing:border-box;margin:0;padding:0}
html,body{width:878px;height:1200px;overflow:hidden}
body{font-family:'Roboto',sans-serif;color:var(--ink);position:relative;
  background:linear-gradient(180deg,var(--gold-top) 0%,#efd690 30%,#e3bb63 60%,var(--gold-bot) 76%);}
.abs{position:absolute}
.topline{left:0;top:0;width:878px;height:2px;background:var(--blue)}
.brand{left:72px;top:18px;display:flex;align-items:center;gap:8px;color:var(--blue);font-weight:700;font-size:21px}
.brand .dot{width:32px;height:32px;border-radius:50%;border:3px solid var(--blue)}
.nav{right:72px;top:26px;display:flex;gap:41px;font-size:12.5px;color:#555;font-weight:300}
.rule{left:72px;width:733px;height:1px;background:#7fb6cf}
.genre{position:absolute;top:101px;font-size:11px;color:#444}
.genre.on{color:var(--blue);text-decoration:underline}
.search{left:421px;top:92px;width:246px;height:34px;border-radius:17px;background:#fff;border:1px solid #ddd;display:flex;align-items:center;padding-left:20px;gap:12px;font-size:12px;color:#bbb;font-weight:300}
.btn{background:linear-gradient(180deg,#2291d6,var(--blue-dark));color:#fff;border-radius:20px;display:flex;align-items:center;justify-content:center;font-weight:500}
.search-btn{left:680px;top:92px;width:125px;height:34px;font-size:14.5px}
.band{left:0;top:150px;width:878px;height:105px;background:var(--blue);box-shadow:0 8px 14px rgba(0,0,0,.18)}
.feature{left:72px;top:178px;display:flex;gap:12px;color:#fff}
.feature h2{font-size:14.5px;font-weight:300}
.feature p{font-size:8.5px;color:#bfe0f5;font-weight:300;line-height:1.45;margin-top:5px}
.pick{position:absolute;top:168px;width:110px;text-align:center;color:#fff;font-size:10px;font-weight:300}
.pick .thumb{width:54px;height:54px;border-radius:50%;border:2px solid #fff;margin:0 auto 6px}
.more{left:680px;top:186px;width:125px;height:34px;border:1px solid #6fb3e0;border-radius:17px;color:#b9dcf3;font-size:11.5px;display:flex;align-items:center;justify-content:center;font-weight:300}
.label{left:72px;top:283px;font-size:12px;color:var(--blue)}
.letters{left:72px;top:310px;display:flex;gap:3.2px}
.letters span{width:25px;height:25px;border:1px solid #7a6a3a;background:#e5c067;display:flex;align-items:center;justify-content:center;font-size:13px;color:#222}
.letters .on{background:#111;color:#fff;border-color:#111}
.sec-title{font-size:12px;font-weight:500;color:#333}
.see{font-size:8px;color:var(--blue)}
.list{background:#fff;border:1px solid #e0e0e0}
.row{height:40.7px;display:flex;align-items:center;border-bottom:1px solid #eee;margin:0 8px;font-size:10.5px}
.row:last-child{border-bottom:0}
.row .ic{width:38px;padding-left:8px}
.row .name{width:110px}
.row .meta{font-size:8px;color:#aaa;font-weight:300}
.acts{margin-left:auto;display:flex;gap:13px;padding-right:6px}
.popular{left:72px;top:750px;width:733px;height:132px;background:#f7f7f7;border:1px solid #e2e2e2;padding:22px 20px}
.popular h3{font-size:12px;font-weight:500;margin-bottom:15px}
.popular p{font-size:8.8px;line-height:15px;color:#666;font-weight:300}
.popular b{color:#333;font-weight:500}
.footer{left:0;top:917px;width:878px;height:283px;background:var(--footer);color:#fff}
.news{left:0;width:878px;text-align:center}
.soc-ic{position:absolute;top:1090px;width:24px;height:24px;border:1.5px solid #ddd;border-radius:50%}
.soc-name{position:absolute;top:1095px;font-size:10.5px;font-weight:300;color:#ddd}
</style>
</head>
<body>
<svg width="0" height="0" style="position:absolute">
  <symbol id="user" viewBox="0 0 20 20"><circle cx="8" cy="6" r="4" fill="#1b7fc1"/><path d="M1 18c0-5 3-7 7-7s7 2 7 7z" fill="#1b7fc1"/><path d="M15 4v8" stroke="#1b7fc1" stroke-width="1.6"/><circle cx="13.5" cy="12" r="1.8" fill="#1b7fc1"/></symbol>
  <symbol id="note" viewBox="0 0 20 20"><path d="M9 2v12" stroke="#1b7fc1" stroke-width="1.6"/><ellipse cx="7" cy="15" rx="3" ry="2.3" fill="#1b7fc1"/><path d="M9 2c2 3 5 3 4 7" stroke="#1b7fc1" stroke-width="1.4" fill="none"/></symbol>
  <symbol id="star" viewBox="0 0 20 20"><path d="M10 1l2.6 6 6.4.6-4.8 4.3 1.4 6.3L10 15l-5.6 3.2 1.4-6.3L1 7.6 7.4 7z" fill="#e9c31a"/></symbol>
  <symbol id="play" viewBox="0 0 20 20"><circle cx="10" cy="10" r="8.5" fill="none" stroke="#8a8a8a" stroke-width="1.6"/><path d="M8 6.5v7l5.5-3.5z" fill="#8a8a8a"/></symbol>
  <symbol id="dl" viewBox="0 0 20 20"><path d="M5 15a4 4 0 0 1 0-8 5 5 0 0 1 9.6-1A4.5 4.5 0 0 1 15 15z" fill="#666"/><path d="M10 8v5M7.5 10.8L10 13.3l2.5-2.5" stroke="#fff" stroke-width="1.6" fill="none"/></symbol>
</svg>

<div class="abs topline"></div>
<div class="abs brand"><span class="dot"></span>Honey Tunes</div>
<nav class="abs nav"><span>Home</span><span>Categories</span><span>Collections</span><span>Top Tens</span></nav>
<div class="abs rule" style="top:67px"></div>
<span class="genre on" style="left:72px">All</span>
<span class="genre" style="left:109px">Song</span>
<span class="genre" style="left:157px">Artist</span>
<span class="genre" style="left:206px">RnB</span>
<span class="genre" style="left:250px">Hip hop</span>
<span class="genre" style="left:310px">rock</span>
<span class="genre" style="left:354px">afro-pop</span>
<div class="abs search"><svg width="15" height="15" viewBox="0 0 16 16"><circle cx="6.5" cy="6.5" r="5" fill="none" stroke="#999" stroke-width="1.4"/><path d="M10 10l4.5 4.5" stroke="#999" stroke-width="1.4"/></svg>Enter Search Text Here</div>
<div class="abs btn search-btn">Search Now</div>

<div class="abs band"></div>
<div class="abs feature">
  <svg width="24" height="50" viewBox="0 0 24 50"><path d="M12 46c-6 0-7-7-2-8M13 2c6 6 2 12-3 17-6 6-5 13 2 13 6 0 7-8 1-8-4 0-5 4-3 6M13 2l-1 44" stroke="#fff" stroke-width="1.8" fill="none"/></svg>
  <div><h2>Feature Play List</h2><p>Pick a mood, song, or artist.<br>We'll play the perfect mix!</p></div>
</div>
<div class="pick" style="left:232px"><div class="thumb" role="img" aria-label="Photo of a guitarist on stage" style="background:radial-gradient(circle,#e77aa0,#a23a6a)"></div>Top 100 Songs</div>
<div class="pick" style="left:338px"><div class="thumb" role="img" aria-label="Photo of an acoustic guitar player" style="background:radial-gradient(circle,#b06a3a,#3c2418)"></div>Top 100 Artists</div>
<div class="pick" style="left:446px"><div class="thumb" role="img" aria-label="Photo of a band group" style="background:radial-gradient(circle,#9a8b6a,#3a2f26)"></div>Good &amp; Evil Play</div>
<div class="pick" style="left:553px"><div class="thumb" role="img" aria-label="Photo of a singer at a studio microphone" style="background:radial-gradient(circle,#d7e4ee,#5b7f9a)"></div>Top 100 Artists</div>
<div class="abs more">More Song Play</div>

<div class="abs label">Artist listing</div>
<div class="abs letters"><span class="on">A</span><span>B</span><span>C</span><span>D</span><span>E</span><span>F</span><span>G</span><span>H</span><span>I</span><span>J</span><span>K</span><span>L</span><span>M</span><span>N</span><span>O</span><span>P</span><span>Q</span><span>R</span><span>S</span><span>T</span><span>U</span><span>V</span><span>W</span><span>X</span><span>Y</span><span>Z</span></div>
<div class="abs" style="left:72px;top:357px;width:733px;height:2px;background:#f3e6bf"></div>

<div class="abs sec-title" style="left:72px;top:379px">TOP 20 ARTISTS</div>
<div class="abs see" style="left:381px;top:382px">See All &gt;&gt;</div>
<div class="abs" style="left:72px;top:404px;width:347px;height:2px;background:var(--blue)"></div>
<div class="abs sec-title" style="left:458px;top:379px">TOP 20 SONGS</div>
<div class="abs see" style="left:767px;top:382px">See All &gt;&gt;</div>
<div class="abs" style="left:458px;top:404px;width:347px;height:2px;background:var(--blue)"></div>

<div class="abs list" style="left:72px;top:426px;width:347px;height:289px">
  <div class="row"><span class="ic"><svg width="18" height="18"><use href="#user"/></svg></span><span class="name">The Velvet Lanterns</span><span class="meta">5 Albums and 36 Songs</span><span class="acts"><svg width="13" height="13"><use href="#star"/></svg><svg width="13" height="13"><use href="#play"/></svg><svg width="14" height="14"><use href="#dl"/></svg></span></div>
  <div class="row"><span class="ic"><svg width="18" height="18"><use href="#user"/></svg></span><span class="name">The Velvet Lanterns</span><span class="meta">5 Albums and 36 Songs</span><span class="acts"><svg width="13" height="13"><use href="#star"/></svg><svg width="13" height="13"><use href="#play"/></svg><svg width="14" height="14"><use href="#dl"/></svg></span></div>
  <div class="row"><span class="ic"><svg width="18" height="18"><use href="#user"/></svg></span><span class="name">The Velvet Lanterns</span><span class="meta">5 Albums and 36 Songs</span><span class="acts"><svg width="13" height="13"><use href="#star"/></svg><svg width="13" height="13"><use href="#play"/></svg><svg width="14" height="14"><use href="#dl"/></svg></span></div>
  <div class="row"><span class="ic"><svg width="18" height="18"><use href="#user"/></svg></span><span class="name">The Velvet Lanterns</span><span class="meta">5 Albums and 36 Songs</span><span class="acts"><svg width="13" height="13"><use href="#star"/></svg><svg width="13" height="13"><use href="#play"/></svg><svg width="14" height="14"><use href="#dl"/></svg></span></div>
  <div class="row"><span class="ic"><svg width="18" height="18"><use href="#user"/></svg></span><span class="name">The Velvet Lanterns</span><span class="meta">5 Albums and 36 Songs</span><span class="acts"><svg width="13" height="13"><use href="#star"/></svg><svg width="13" height="13"><use href="#play"/></svg><svg width="14" height="14"><use href="#dl"/></svg></span></div>
  <div class="row"><span class="ic"><svg width="18" height="18"><use href="#user"/></svg></span><span class="name">The Velvet Lanterns</span><span class="meta">5 Albums and 36 Songs</span><span class="acts"><svg width="13" height="13"><use href="#star"/></svg><svg width="13" height="13"><use href="#play"/></svg><svg width="14" height="14"><use href="#dl"/></svg></span></div>
  <div class="row"><span class="ic"><svg width="18" height="18"><use href="#user"/></svg></span><span class="name">The Velvet Lanterns</span><span class="meta">5 Albums and 36 Songs</span><span class="acts"><svg width="13" height="13"><use href="#star"/></svg><svg width="13" height="13"><use href="#play"/></svg><svg width="14" height="14"><use href="#dl"/></svg></span></div>
</div>

<div class="abs list" style="left:458px;top:426px;width:347px;height:289px">
  <div class="row"><span class="ic"><svg width="16" height="18"><use href="#note"/></svg></span><span class="name" style="width:170px">The Velvet Lanterns</span><span class="meta">00.25</span><span class="acts"><svg width="13" height="13"><use href="#star"/></svg><svg width="13" height="13"><use href="#play"/></svg><svg width="14" height="14"><use href="#dl"/></svg></span></div>
  <div class="row"><span class="ic"><svg width="16" height="18"><use href="#note"/></svg></span><span class="name" style="width:170px">The Velvet Lanterns</span><span class="meta">00.25</span><span class="acts"><svg width="13" height="13"><use href="#star"/></svg><svg width="13" height="13"><use href="#play"/></svg><svg width="14" height="14"><use href="#dl"/></svg></span></div>
  <div class="row"><span class="ic"><svg width="16" height="18"><use href="#note"/></svg></span><span class="name" style="width:170px">The Velvet Lanterns</span><span class="meta">00.25</span><span class="acts"><svg width="13" height="13"><use href="#star"/></svg><svg width="13" height="13"><use href="#play"/></svg><svg width="14" height="14"><use href="#dl"/></svg></span></div>
  <div class="row"><span class="ic"><svg width="16" height="18"><use href="#note"/></svg></span><span class="name" style="width:170px">The Velvet Lanterns</span><span class="meta">00.25</span><span class="acts"><svg width="13" height="13"><use href="#star"/></svg><svg width="13" height="13"><use href="#play"/></svg><svg width="14" height="14"><use href="#dl"/></svg></span></div>
  <div class="row"><span class="ic"><svg width="16" height="18"><use href="#note"/></svg></span><span class="name" style="width:170px">The Velvet Lanterns</span><span class="meta">00.25</span><span class="acts"><svg width="13" height="13"><use href="#star"/></svg><svg width="13" height="13"><use href="#play"/></svg><svg width="14" height="14"><use href="#dl"/></svg></span></div>
  <div class="row"><span class="ic"><svg width="16" height="18"><use href="#note"/></svg></span><span class="name" style="width:170px">The Velvet Lanterns</span><span class="meta">00.25</span><span class="acts"><svg width="13" height="13"><use href="#star"/></svg><svg width="13" height="13"><use href="#play"/></svg><svg width="14" height="14"><use href="#dl"/></svg></span></div>
  <div class="row"><span class="ic"><svg width="16" height="18"><use href="#note"/></svg></span><span class="name" style="width:170px">The Velvet Lanterns</span><span class="meta">00.25</span><span class="acts"><svg width="13" height="13"><use href="#star"/></svg><svg width="13" height="13"><use href="#play"/></svg><svg width="14" height="14"><use href="#dl"/></svg></span></div>
</div>

<section class="abs popular">
  <h3>POPULAR LAST ADDED</h3>
  <p>There are many variations of passages of <b>Lorem Ipsum</b> available But the majority have suffered <b>alteration in some form</b>, by injected humour, or randomised words which don't look even <b>slightly believable</b>. If you are going to use a passage of Lorem Ipsum, you need to be sure there isn't <b>anything embarrassing</b> hidden in the middle of text. All the Lorem Ipsum rators on the Internet tend to repeat predefined <b>chunks as necessary</b>, making this the first true generator on the Internet. It uses a dictionary of over 200 Latin words, combined with a handful of model sentence structures, to generate Lorem Ipsum which looks reasonable. The generated Lorem Ipsum is therefore <b>always free from repetition</b></p>
</section>

<footer class="abs footer"></footer>
<div class="abs news" style="top:949px;font-size:12px;font-weight:500;color:#fff">SUBSCRIBE TO OUR NEWSLETTER</div>
<div class="abs" style="left:262px;top:984px;width:354px;height:1px;background:#3a3a3a"></div>
<div class="abs news" style="top:995px;font-size:8px;color:#555">Your Email Here</div>
<div class="abs" style="left:262px;top:1016px;width:354px;height:1px;background:#3a3a3a"></div>
<div class="abs btn" style="left:376px;top:1038px;width:125px;height:34px;font-size:11.5px">Subscribe Now</div>

<span class="soc-ic" style="left:182px"></span><span class="soc-name" style="left:218px">Kindred</span>
<span class="soc-ic" style="left:294px"></span><span class="soc-name" style="left:332px">Murmur</span>
<span class="soc-ic" style="left:394px"></span><span class="soc-name" style="left:432px">Shutterloop</span>
<span class="soc-ic" style="left:506px"></span><span class="soc-name" style="left:542px">Orbit +</span>
<span class="soc-ic" style="left:610px"></span><span class="soc-name" style="left:650px">Moodwall</span>

<div class="abs" style="left:182px;top:1136px;width:620px;height:1px;background:#2c2c2c"></div>
<div class="abs news" style="top:1156px;font-size:9.5px;color:#555;font-weight:300">Copyrights@2016 Company Name @ All rights reserved</div>
</body>
</html>
```